Company director needs a business card design

I am a semi-retired former senior finance executive who sits on a number of public and private company boards and do some consulting work. I work largely with emerging businesses but deal regularly with top end of town lawyers, bankers etc. I need a thoughtful but relatively conservative design which would also resonate with my younger client base. Some colour would be good. Information limited to name, address, office tel, mobile and email.

Finance

```html
<!DOCTYPE html>
<html lang="en">
<head>
<meta charset="utf-8">
<title>Marlo — Business Card</title>
<link rel="stylesheet" href="https://fonts.googleapis.com/css2?family=Open+Sans:wght@400;600;700&display=swap">
<style>
  :root {
    --backdrop: #1d1d1f;
    --card-blue: #2f3397;
    --forest: #2c3a2a;
    --band-white: #f6f6f6;
    --ink: #2a2a2a;
    --name-white: #ffffff;
    --title-blue: #3b4fc4;
  }
  * { margin: 0; padding: 0; box-sizing: border-box; }
  html, body {
    width: 1200px; height: 800px; overflow: hidden;
    background: var(--backdrop);
    font-family: "Open Sans", Arial, sans-serif;
  }
  .business-card {
    position: absolute; left: 110px; top: 120px;
    width: 980px; height: 560px;
    background: var(--card-blue);
    overflow: hidden;
  }
  .accent-shape {
    position: absolute; left: 0; top: 0;
    width: 980px; height: 560px;
  }
  .name-tab {
    position: absolute; right: 0; top: 0;
    width: 270px; height: 84px;
    background: var(--forest);
    border-bottom-left-radius: 42px;
    display: flex; flex-direction: column; justify-content: center;
    padding-left: 84px;
  }
  .holder-name {
    color: var(--name-white);
    font-weight: 700; font-size: 26px; line-height: 1.1;
  }
  .holder-title {
    color: var(--title-blue);
    font-weight: 600; font-size: 14px; line-height: 1.2;
  }
  .contact-band {
    position: absolute; left: 0; top: 250px;
    width: 700px; height: 150px;
    background: var(--band-white);
    border-radius: 0 75px 75px 0;
  }
  .contact-line {
    position: absolute;
    color: var(--ink);
    font-size: 20px; font-weight: 400; white-space: nowrap;
  }
  .office-tel { left: 60px; top: 84px; }
  .mobile-tel { left: 84px; top: 112px; }
  .address { left: 372px; top: 20px; }
  .email { left: 372px; top: 48px; }
</style>
</head>
<body>
  <div class="business-card">
    <svg class="accent-shape" viewBox="0 0 980 560" aria-hidden="true">
      <polygon points="322,140 470,250 450,470" fill="var(--forest)"/>
    </svg>

    <div class="name-tab">
      <span class="holder-name">Marlo</span>
      <span class="holder-title">Director</span>
    </div>

    <div class="contact-band">
      <span class="contact-line office-tel">4870-2193</span>
      <span class="contact-line mobile-tel">00 987 654 321</span>
      <span class="contact-line address">214 Harrow Lane, BC</span>
      <span class="contact-line email">email-marlo214@mailbox.com</span>
    </div>
  </div>
</body>
</html>
```